Unique Business Card Design

Unique Business Card design for our orthotic and prosthetic company. Our logo is on our website, color is light blue. Unique shape (artificial leg shaped, vertical, etc..) preferred. Logo, business name, individual name and basic demographics needed.

Industry/Entity Type

Business

Contact Information for Business Card

Logo, Industry, Phone # Logo, "Prosthetic & Orthotic Services" Place to add individual name and contact info

Colors
cee9f5

Requirements
Must have
• The icon must be there, placement of "Prosthetic & Orthotic Services" can be moved
Nice to have
• Like the mix of light blue, and a little darker blue. One design included the icons from my website which was a nice touch

```html
<!DOCTYPE html>
<html lang="en">
<head>
<meta charset="utf-8">
<title>Kestrel Limb Inc. – Business Card</title>
<link rel="stylesheet" href="https://fonts.googleapis.com/css2?family=Open+Sans:wght@400;600;700&family=Crimson+Text:ital@1&display=swap">
<style>
  :root {
    --brand-blue: #1560ad;
    --ink: #4a4a4a;
    --paper: #ffffff;
    --backdrop: #3b3b3b;
  }
  * { box-sizing: border-box; margin: 0; padding: 0; }
  html, body { width: 1105px; height: 1200px; overflow: hidden; }
  body {
    background: var(--backdrop);
    font-family: "Open Sans", Arial, sans-serif;
    position: relative;
  }
  .card {
    position: absolute;
    left: 192px;
    width: 720px;
    height: 410px;
    overflow: hidden;
  }
  .card--front { top: 167px; background: var(--paper); }
  .card--back { top: 623px; background: var(--brand-blue); }

  .brand-dot {
    position: absolute;
    border-radius: 50%;
  }
  .card--front .brand-dot {
    left: 45px; top: 49px; width: 78px; height: 78px;
    background: var(--brand-blue);
  }
  .card--back .brand-dot {
    left: 137px; top: 148px; width: 116px; height: 116px;
    background: var(--paper);
  }
  .brand-name {
    position: absolute;
    font-weight: 600;
    white-space: nowrap;
    line-height: 1;
  }
  .card--front .brand-name { left: 145px; top: 63px; font-size: 23px; color: var(--brand-blue); }
  .card--back .brand-name { left: 284px; top: 167px; font-size: 33px; color: var(--paper); }
  .tagline {
    position: absolute;
    font-family: "Crimson Text", Georgia, serif;
    font-style: italic;
    white-space: nowrap;
    line-height: 1;
  }
  .card--front .tagline { left: 157px; top: 92px; font-size: 14px; color: var(--brand-blue); }
  .card--back .tagline { left: 298px; top: 218px; font-size: 20px; color: var(--paper); }

  .address {
    position: absolute;
    left: 44px; top: 180px;
    font-size: 19px;
    line-height: 28px;
    color: var(--ink);
    font-style: normal;
  }
  .contact-list {
    position: absolute;
    left: 44px; top: 238px;
    list-style: none;
    font-size: 19px;
    color: var(--ink);
  }
  .contact-list li {
    display: flex;
    align-items: center;
    height: 27.7px;
    white-space: nowrap;
  }
  .contact-list svg {
    width: 18px; height: 18px;
    margin-right: 12px;
    fill: var(--brand-blue);
    flex: none;
  }
  .person {
    position: absolute;
    right: 47px; top: 250px;
    text-align: right;
    color: var(--brand-blue);
  }
  .person-name { font-size: 26px; font-weight: 600; line-height: 32px; }
  .person-title { font-size: 18px; font-weight: 700; line-height: 24px; }
  .edge-tab {
    position: absolute;
    left: 708px; top: 253px;
    width: 50px; height: 50px;
    border-radius: 50%;
    background: var(--brand-blue);
  }
</style>
</head>
<body>
  <section class="card card--front">
    <span class="brand-dot"></span>
    <div class="brand-name">KESTREL LIMB INC.</div>
    <div class="tagline">Prosthetic &amp; Orthotic Services</div>

    <address class="address">2210 W. 14th St.<br>Riverton, NY 11480</address>

    <ul class="contact-list">
      <li><svg viewBox="0 0 24 24"><path d="M6.6 10.8a15.2 15.2 0 0 0 6.6 6.6l2.2-2.2c.3-.3.7-.4 1-.2 1.1.4 2.3.6 3.6.6.6 0 1 .4 1 1V20c0 .6-.4 1-1 1A17 17 0 0 1 3 4c0-.6.4-1 1-1h3.5c.6 0 1 .4 1 1 0 1.3.2 2.5.6 3.6.1.3 0 .7-.2 1z"/></svg>555.014.2200</li>
      <li><svg viewBox="0 0 24 24"><path d="M7 1h10a2 2 0 0 1 2 2v18a2 2 0 0 1-2 2H7a2 2 0 0 1-2-2V3a2 2 0 0 1 2-2zm0 3v14h10V4zm5 15.5a1.2 1.2 0 1 0 0 2.4 1.2 1.2 0 0 0 0-2.4z"/></svg>555.014.3870</li>
      <li><svg viewBox="0 0 24 24"><path d="M6 2h12v5H6zM3 8h18a2 2 0 0 1 2 2v7h-4v5H5v-5H1v-7a2 2 0 0 1 2-2zm4 7v5h10v-5z"/></svg>555-0196431</li>
      <li><svg viewBox="0 0 24 24"><path d="M2 5h20v14H2zm2 2v.5l8 5.5 8-5.5V7z"/></svg>mholloway@kestrellimb.com</li>
      <li><svg viewBox="0 0 24 24"><path d="M12 2a10 10 0 1 0 0 20 10 10 0 0 0 0-20zm-1 17.9A8 8 0 0 1 4.2 10.5L9 15v1a2 2 0 0 0 2 2zm6.9-2.5A2 2 0 0 0 16 16h-1v-3a1 1 0 0 0-1-1H8v-2h2a1 1 0 0 0 1-1V7h2a2 2 0 0 0 2-2v-.4a8 8 0 0 1 2.9 12.8z"/></svg>www.kestrellimb.com</li>
    </ul>

    <div class="person">
      <div class="person-name">MAREN HOLLOWAY</div>
      <div class="person-title">CO LPO</div>
    </div>
    <span class="edge-tab"></span>
  </section>

  <section class="card card--back">
    <span class="brand-dot"></span>
    <div class="brand-name">KESTREL LIMB INC.</div>
    <div class="tagline">Prosthetic &amp; Orthotic Services</div>
  </section>
</body>
</html>
```